BrivoTerna. Lantern of the Steady Harvest. Business card

Professional business card for BrivoTerna (Lantern of the Steady Harvest)
My rationale: Strategy-> Execution-> Results-> Value that lead to the BrivoTerna name: We put the Lantern of the Steady Harvest.
We deliver value to our customers helping them at defining a good strategy (cyan arrow). 90% of well formulated strategies fail due to poor execution so we also consider strategical execution very important (green arrow). Due to the execution we obtain the results (blue arrow). Finally, the results provide feedback to redefine strategy, and the new strategy has to be executed and new results obtained providing new feedback and on and on. It's like a wheel that finally, must create corporate value: value for shareholders, staholders, employees, providers...-

Target Market(s)

CEOs and steering comitees , invewrnent funds

Industry/Entity Type

Business Consultant

Contact Information for Business Card

Teodoro Vinsquel
CEO & Founder
teodoro.vinsquel@brivoterna-example.com
Mobile: +34 655.803.912
www.brivoterna-example.com

Colors

Designer to choose colors to be used in the design.

Requirements
Nice to have
• Nice to hace the words: Strategy, execution, results
• Nice to vave the claim: Lantern of the Steady Harvest
• The three colors should be shown:
• cyan for STRATEGY
• green for EXECUTION
• blue for RESULTS
Should not have
• Complete black background

```html
<!DOCTYPE html>
<html lang="en">
<head>
<meta charset="utf-8">
<title>BrivoTerna — Business Card</title>
<link href="https://fonts.googleapis.com/css2?family=Lato:wght@400;700&display=swap" rel="stylesheet">
<style>
  :root {
    --backdrop: #dedede;
    --card: #ffffff;
    --navy: #253b90;
    --green: #8dc63f;
    --cyan: #29a9df;
    --grey-text: #8a8a8a;
    --shadow: rgba(0,0,0,0.55);
    --wash-lavender: #e3e3f0;
    --wash-green: #eff5e4;
  }
  * { margin: 0; padding: 0; box-sizing: border-box; }
  html, body {
    width: 1200px; height: 960px; overflow: hidden;
    background: var(--backdrop);
    font-family: "Lato", sans-serif;
  }
  .card {
    position: absolute;
    left: 281px;
    width: 655px;
    height: 374px;
    background: var(--card);
    border-radius: 24px;
    box-shadow: 0 4px 0 -1px var(--shadow), 0 6px 6px rgba(0,0,0,0.12);
    overflow: hidden;
  }
  .card--front { top: 80px; }
  .card--back { top: 506px; }

  .brand-wash {
    position: absolute;
    left: 0; top: 0;
    width: 245px; height: 374px;
    background: linear-gradient(160deg, var(--wash-lavender) 0%, var(--wash-lavender) 45%, var(--wash-green) 75%, #ffffff 100%);
    opacity: 0.8;
  }

  .brand {
    display: flex;
    align-items: center;
    gap: 10px;
    color: var(--navy);
    font-weight: 700;
    letter-spacing: -0.5px;
  }
  .brand__dot {
    border-radius: 50%;
    background: var(--navy);
    flex: none;
  }
  .card--front .brand {
    position: absolute;
    left: 282px; top: 118px;
    font-size: 36px;
    line-height: 1;
  }
  .card--front .brand__dot { width: 16px; height: 16px; }

  .person {
    position: absolute;
    left: 282px; top: 188px;
  }
  .person__name {
    color: var(--navy);
    font-weight: 700;
    font-size: 26px;
    line-height: 1.1;
  }
  .person__role {
    color: var(--grey-text);
    font-size: 17px;
    margin-top: 6px;
  }

  .contact {
    position: absolute;
    left: 282px; top: 262px;
    list-style: none;
    color: var(--grey-text);
    font-size: 16.5px;
  }
  .contact__item {
    display: flex;
    align-items: center;
    gap: 7px;
    height: 24px;
  }
  .contact__icon { width: 13px; height: 13px; flex: none; }

  .card--back .brand {
    position: absolute;
    left: 0; right: 0; top: 200px;
    justify-content: center;
    font-size: 50px;
    line-height: 1;
  }
  .card--back .brand__dot { width: 22px; height: 22px; }

  .tagline {
    position: absolute;
    left: 0; right: 0; top: 283px;
    text-align: center;
    font-size: 17.5px;
    letter-spacing: 0.3px;
    color: var(--grey-text);
  }
  .tagline__strategy { color: var(--cyan); }
  .tagline__execution { color: var(--green); }
  .tagline__results { color: var(--navy); }
  .tagline__sep { margin: 0 6px; }
</style>
</head>
<body>

<section class="card card--front">
  <div class="brand-wash" role="img" aria-label="Faint brand decoration in soft lavender and green tones"></div>

  <div class="brand">
    <span class="brand__dot"></span>
    <span class="brand__name">BrivoTerna</span>
  </div>

  <div class="person">
    <h1 class="person__name">Teodoro Vinsquel</h1>
    <p class="person__role">CEO &amp; Founder</p>
  </div>

  <ul class="contact">
    <li class="contact__item">
      <svg class="contact__icon" viewBox="0 0 16 16" aria-hidden="true">
        <path d="M4 1 L6.5 4 L5 6 Q6.5 9.5 10 11 L12 9.5 L15 12 L13 15 Q5 14 1 3 Z" fill="var(--navy)"/>
      </svg>
      <span>+34 655.803.912</span>
    </li>
    <li class="contact__item">
      <svg class="contact__icon" viewBox="0 0 16 16" aria-hidden="true">
        <rect x="1" y="3.5" width="14" height="9" fill="var(--navy)"/>
        <path d="M1.5 4 L8 9 L14.5 4" stroke="#fff" stroke-width="1.2" fill="none"/>
      </svg>
      <span>teodoro.vinsquel@brivoterna-example.com</span>
    </li>
    <li class="contact__item">
      <svg class="contact__icon" viewBox="0 0 16 16" aria-hidden="true">
        <g fill="none" stroke="var(--navy)" stroke-width="1.3">
          <circle cx="8" cy="8" r="6.5"/>
          <ellipse cx="8" cy="8" rx="3" ry="6.5"/>
          <line x1="1.5" y1="8" x2="14.5" y2="8"/>
          <line x1="2.5" y1="4.5" x2="13.5" y2="4.5"/>
          <line x1="2.5" y1="11.5" x2="13.5" y2="11.5"/>
        </g>
      </svg>
      <span>www.brivoterna-example.com</span>
    </li>
  </ul>
</section>

<section class="card card--back">
  <div class="brand">
    <span class="brand__dot"></span>
    <span class="brand__name">BrivoTerna</span>
  </div>
  <p class="tagline">
    <span class="tagline__strategy">STRATEGY</span><span class="tagline__sep">-</span><span class="tagline__execution">EXECUTION</span><span class="tagline__sep">-</span><span class="tagline__results">RESULTS</span>
  </p>
</section>

</body>
</html>
```